RK Donnelly & Associates

Create a website encompassing design work already carried out for business card.
Small accounting practice, business accounting and management, superannuation, audit, taxation.

```html
<!DOCTYPE html>
<html lang="en">
<head>
<meta charset="utf-8">
<title>RK Donnelly &amp; Associates</title>
<link href="https://fonts.googleapis.com/css2?family=Open+Sans:ital,wght@0,400;0,600;0,700;1,400&display=swap" rel="stylesheet">
<style>
:root{
  --side:#262626;
  --page:#ffffff;
  --ink:#222222;
  --body:#444444;
  --muted:#666666;
  --blue:#72a9de;
  --nav:#1c1c1c;
  --nav-line:#3a3a3a;
  --icon:#c9c9c9;
  --rule:#cfcfcf;
  --tick:#7cbc3a;
}
*{margin:0;padding:0;box-sizing:border-box}
html,body{width:1193px;height:1200px;overflow:hidden;background:var(--side)}
body{font-family:Arial,Helvetica,sans-serif;color:var(--body)}
.page{position:absolute;left:170px;top:0;width:852px;height:1200px;background:var(--page)}
.abs{position:absolute}
.brand{left:22px;top:6px;display:flex;align-items:center;gap:10px}
.brand-mark{width:56px;height:56px;background:var(--blue)}
.brand-name{font-family:'Open Sans',sans-serif;font-weight:600;font-size:22px;line-height:25px;color:#666;width:160px}
.tagline{left:22px;top:81px;font-size:10.5px;color:#333}
.follow{left:421px;top:44px;display:flex;align-items:center;gap:9px;font-size:12px;color:#333}
.follow .dot{width:27px;height:27px;border-radius:50%;background:var(--icon)}
.follow span{margin-right:2px}
.call{left:669px;top:37px;display:flex;align-items:center;gap:10px}
.call .ring{width:39px;height:39px;border-radius:50%;background:var(--blue);display:flex;align-items:center;justify-content:center}
.call small{display:block;font-size:12px;color:#444}
.call strong{display:block;font-weight:400;font-size:16px;color:#111;margin-top:2px}
.nav{left:22px;top:103px;width:809px;height:48px;background:var(--nav);display:flex}
.nav a{color:#fff;text-decoration:none;font-family:'Open Sans',sans-serif;font-weight:600;font-size:11.5px;display:flex;align-items:center;justify-content:center;border-right:1px solid var(--nav-line);height:100%}
.nav a:last-child{border-right:0}
.hero{left:22px;top:153px;width:809px;height:271px;background:linear-gradient(90deg,#dcdcdc 0%,#cfcfcf 45%,#8f8f8f 62%,#3a3a3a 72%,#b7b7b7 90%,#c8c8c8 100%)}
.hero h1{position:absolute;left:50px;top:76px;font-family:'Open Sans',sans-serif;font-weight:700;font-size:27px;color:#1e1e1e;letter-spacing:.3px}
.hero p{position:absolute;left:51px;top:118px;width:380px;font-family:'Open Sans',sans-serif;font-size:14px;line-height:23px;color:#222}
.hero .arrows{position:absolute;left:50px;top:195px;display:flex;gap:1px}
.hero .arrows span{width:23px;height:22px;background:#a8a8a8;display:flex;align-items:center;justify-content:center}
.services-lead{left:22px;top:441px;font-family:'Open Sans',sans-serif;font-size:14.5px;color:#222}
.services-lead em{font-size:12.5px;color:#444}
.tiles{left:22px;top:475px;width:809px;height:140px;display:flex;gap:1px}
.tile{flex:1;position:relative}
.tile .cap{position:absolute;left:0;bottom:0;width:168px;height:31px;background:var(--blue);color:#fff;font-family:'Open Sans',sans-serif;font-size:11px;display:flex;align-items:center;justify-content:center}
h2{font-family:'Open Sans',sans-serif;font-weight:400;font-size:14.5px;color:#222}
.touch-h{left:22px;top:654px}
.touch-p{left:22px;top:680px;width:640px;font-size:10.5px;line-height:19.5px;color:#333}
.btn{background:var(--blue);color:#fff;font-family:'Open Sans',sans-serif;font-size:11.5px;display:flex;align-items:center;justify-content:center}
.touch-btn{left:702px;top:676px;width:129px;height:32px}
.rule{left:22px;top:742px;width:809px;height:2px;background:var(--rule)}
.about-h{left:22px;top:779px}
.about-img{left:22px;top:816px;width:204px;height:137px;background:linear-gradient(120deg,#e9e9e9,#bdbdbd 55%,#3b3b3b)}
.about-p{left:255px;top:813px;width:280px;font-size:10.5px;line-height:19.6px;color:#333}
.about-btn{left:255px;top:919px;width:130px;height:33px}
.feat-h{left:559px;top:779px}
.features{left:559px;top:806px;width:270px;list-style:none}
.features li{position:relative;padding-left:18px;font-family:'Open Sans',sans-serif;font-style:italic;font-size:11px;line-height:19.6px;color:#333;margin-bottom:9px}
.features svg{position:absolute;left:0;top:4px}
.shadow{left:45px;top:995px;width:765px;height:10px;background:radial-gradient(ellipse at 50% 0%,rgba(0,0,0,.18),rgba(0,0,0,0) 70%)}
.partners{left:22px;top:1025px;width:809px;height:36px;display:flex;justify-content:space-between;align-items:center;padding:0 8px}
.partner{display:flex;align-items:center;gap:6px;font-family:'Open Sans',sans-serif;font-weight:600;font-size:14px;color:#3d6fa8}
.partner i{width:20px;height:20px;border-radius:50%;background:#9dbfe0;display:block}
.footer{left:22px;top:1090px;width:809px;height:91px;background:var(--nav)}
.footer .f-brand{position:absolute;left:26px;top:22px;display:flex;align-items:center;gap:8px}
.footer .f-mark{width:42px;height:42px;background:var(--blue)}
.footer .f-name{font-family:'Open Sans',sans-serif;font-weight:600;font-size:15px;line-height:17px;color:#fff;width:110px}
.footer .divider{position:absolute;left:187px;top:24px;width:1px;height:49px;background:#555}
.footer .links{position:absolute;left:209px;top:26px;font-size:10.5px;color:#ccc;white-space:nowrap}
.footer .links span{margin:0 12px;color:#999}
.footer .copy{position:absolute;left:209px;top:53px;font-size:10.5px;color:#ccc}
</style>
</head>
<body>
<div class="page">
  <div class="abs brand"><div class="brand-mark"></div><div class="brand-name">RK Donnelly &amp; Associates</div></div>
  <div class="abs tagline">Account - Business Solutions - Management - Superannuation - Audit</div>

  <div class="abs follow"><span>FOLLOW US :</span><div class="dot" aria-label="Social profile"></div><div class="dot" aria-label="Social profile"></div><div class="dot" aria-label="Social profile"></div><div class="dot" aria-label="Social profile"></div></div>

  <div class="abs call">
    <div class="ring"><svg width="20" height="20" viewBox="0 0 24 24"><path fill="#fff" d="M6.6 10.8c1.4 2.8 3.8 5.1 6.6 6.6l2.2-2.2c.3-.3.7-.4 1-.2 1.1.4 2.3.6 3.6.6.6 0 1 .4 1 1V20c0 .6-.4 1-1 1C10.6 21 3 13.4 3 4c0-.6.4-1 1-1h3.5c.6 0 1 .4 1 1 0 1.3.2 2.5.6 3.6.1.3 0 .7-.2 1l-2.3 2.2z"/></svg></div>
    <div><small>CALL US :</small><strong>( 1380 ) 555 014</strong></div>
  </div>

  <nav class="abs nav">
    <a style="width:52px" aria-label="Home"><svg width="11" height="10" viewBox="0 0 12 11"><path fill="#fff" d="M6 0 0 5.5h1.7V11h3V7.5h2.6V11h3V5.5H12z"/></svg></a>
    <a style="width:127px">ABOUT US</a>
    <a style="width:149px">WHAT WE DO?</a>
    <a style="width:115px">SERVICES</a>
    <a style="width:88px">FAQ'S</a>
    <a style="width:123px">FEATURES</a>
    <a style="width:148px">TESTIMONIALS</a>
    <a style="width:107px">CONTACT US</a>
  </nav>

  <section class="abs hero" role="img" aria-label="Photo of a thoughtful businessman in glasses and suit">
    <h1>RK DONNELLY &amp; ASSOCIATES</h1>
    <p>WE DO SMALL ACCOUNTING PRACTICE, BUSINESS ACCOUNTING AND MANAGEMENT, SUPERANNUATION, AUDIT, TAXATION.</p>
    <div class="arrows">
      <span><svg width="8" height="12" viewBox="0 0 8 12"><path d="M6 1 1 6l5 5" stroke="#fff" fill="none" stroke-width="1.3"/></svg></span>
      <span><svg width="8" height="12" viewBox="0 0 8 12"><path d="m2 1 5 5-5 5" stroke="#fff" fill="none" stroke-width="1.3"/></svg></span>
    </div>
  </section>

  <p class="abs services-lead">OUR SERVICES. <em>We do Small accounting practice, business accounting and management, superannuation, audit, taxation.</em></p>

  <div class="abs tiles">
    <div class="tile" role="img" aria-label="Photo of colleagues reviewing work at a computer" style="background:linear-gradient(90deg,#f2f2f2,#d9d9d9 60%,#c6c6c6)"><div class="cap">ACCOUNTING PRACTICE</div></div>
    <div class="tile" role="img" aria-label="Photo of two businessmen talking in an office" style="background:linear-gradient(90deg,#8a97a8,#c9ccd0 45%,#5e6673)"><div class="cap">BUSINESS ACCOUNTING</div></div>
    <div class="tile" role="img" aria-label="Photo of a handshake over a world map" style="background:linear-gradient(90deg,#2e2e2e,#777 50%,#3c3c3c)"><div class="cap">MANAGEMENT</div></div>
  </div>

  <h2 class="abs touch-h">GET IN TOUCH</h2>
  <p class="abs touch-p">Lorem Ipsum is simply dummy text of the printing and typesetting industry. Lorem Ipsum has been the industry's standard dummy text ever since the 1500s, when an unknown printer took a galley of type and scrambled it to make a type specimen book.</p>
  <div class="abs btn touch-btn">CONTACT NOW</div>

  <div class="abs rule"></div>

  <h2 class="abs about-h">ABOUT RK DONNELLY &amp; ASSOCIATES</h2>
  <div class="abs about-img" role="img" aria-label="Photo of two colleagues working over documents at a desk"></div>
  <p class="abs about-p">Lorem Ipsum is simply dummy text of the printing and type-setting industry. Lorem Ipsum has been the industry's stan-dard dummy text ever since the 1500s, when an unknown printer took a galley of type and scrambled it to make a type specimen book.</p>
  <div class="abs btn about-btn">READ MORE INFO</div>

  <h2 class="abs feat-h">FEATURES</h2>
  <ul class="abs features">
    <li><svg width="13" height="11" viewBox="0 0 13 11"><path d="M1 6l4 4 7-9" stroke="var(--tick)" stroke-width="2" fill="none"/></svg>Lorem Ipsum is simply dummy text of the printing</li>
    <li><svg width="13" height="11" viewBox="0 0 13 11"><path d="M1 6l4 4 7-9" stroke="var(--tick)" stroke-width="2" fill="none"/></svg>Lorem Ipsum is simply dummy text of the printing and typesetting industry.</li>
    <li><svg width="13" height="11" viewBox="0 0 13 11"><path d="M1 6l4 4 7-9" stroke="var(--tick)" stroke-width="2" fill="none"/></svg>Lorem Ipsum is simply dummy text of the printing</li>
    <li><svg width="13" height="11" viewBox="0 0 13 11"><path d="M1 6l4 4 7-9" stroke="var(--tick)" stroke-width="2" fill="none"/></svg>Lorem Ipsum is simply dummy text of the printing and typesetting industry.</li>
  </ul>

  <div class="abs shadow"></div>
  <div class="abs partners">
    <div class="partner"><i></i>Harbourline Leisure</div>
    <div class="partner">Vantor Group</div>
    <div class="partner">Coinvale</div>
    <div class="partner"><i></i>Pell &amp; Row Archives</div>
    <div class="partner">Ostrava Technology</div>
  </div>

  <footer class="abs footer">
    <div class="f-brand"><div class="f-mark"></div><div class="f-name">RK Donnelly &amp; Associates.</div></div>
    <div class="divider"></div>
    <div class="links">Home<span>|</span>About Us<span>|</span>What we do?<span>|</span>Services<span>|</span>Faq's<span>|</span>Features<span>|</span>Testimonials<span>|</span>Contact us</div>
    <div class="copy">© 2014. RK Donnelly &amp; Associates. All rights reserved.</div>
  </footer>
</div>
</body>
</html>
```